Veluxa Bone & Motion Business Card

Need a business card using the logo provided. I want brand side of the card to be grey with the logo in the center of the card in white.

On the other side I leave to the designers

Target Market(s)

Personal Injury Attorneys

Industry/Entity Type

Medical

Contact Information for Business Card

Name, CEO. Cell Phone, (Hialeah, Address, Phone) (Homestead, Address, Phone) (Tallahassee, Address, Phone)

Colors

Designer to choose only greyscale colors for use in the design.

Requirements
Must have
• Logo by itself on one side

```html
<!DOCTYPE html>
<html lang="en">
<head>
<meta charset="utf-8">
<title>Veluxa Bone &amp; Motion – Business Card</title>
<link rel="stylesheet" href="https://fonts.googleapis.com/css2?family=Montserrat:wght@400;500;600&display=swap">
<style>
  :root {
    --backdrop: #b0b0ab;
    --card-dark: #232323;
    --card-grey: #4d4d4d;
    --card-edge: #8a8a8a;
    --accent: #b9b9b9;
    --text: #f2f2f2;
    --logo-white: #ffffff;
  }
  * { box-sizing: border-box; margin: 0; padding: 0; }
  html, body {
    width: 1200px; height: 801px; overflow: hidden;
    background: var(--backdrop);
    font-family: "Montserrat", sans-serif;
  }
  .stage {
    width: 1200px; height: 801px;
    display: flex; align-items: center; justify-content: center; gap: 40px;
  }
  .card {
    width: 540px; height: 309px;
    border-radius: 18px;
    border-bottom: 2px solid var(--card-edge);
    position: relative;
    box-shadow: 0 10px 24px rgba(0,0,0,0.25);
  }
  /* contact side */
  .card--contact {
    background: var(--card-dark);
    display: flex; align-items: center;
  }
  .brand-block {
    width: 250px; display: flex; justify-content: center;
  }
  .brand-name {
    font-weight: 600;
    letter-spacing: 0.12em;
    text-transform: uppercase;
    text-align: left;
  }
  .card--contact .brand-name {
    color: var(--accent);
    font-size: 22px;
    line-height: 1.15;
  }
  .divider {
    width: 1.5px; height: 230px; background: var(--accent);
  }
  .contact {
    padding-left: 26px;
    color: var(--text);
    font-size: 11.5px;
    line-height: 16px;
  }
  .contact__name {
    color: var(--accent);
    font-weight: 600; font-size: 19px; line-height: 22px;
    text-transform: uppercase; letter-spacing: 0.02em;
  }
  .contact__title { font-size: 13px; margin-bottom: 4px; }
  .contact__row { display: flex; align-items: center; gap: 6px; }
  .contact__row svg { width: 10px; height: 10px; flex: none; }
  .office { margin-top: 2px; }
  .office__phone { color: var(--accent); }
  /* brand side */
  .card--brand {
    background: var(--card-grey);
    display: flex; align-items: center; justify-content: center;
  }
  .card--brand .brand-name {
    color: var(--logo-white);
    font-size: 40px;
    line-height: 1.1;
  }
</style>
</head>
<body>
<main class="stage">
  <section class="card card--contact">
    <div class="brand-block">
      <p class="brand-name">Veluxa<br>Bone &amp; Motion</p>
    </div>
    <div class="divider"></div>
    <div class="contact">
      <p class="contact__name">Daniel Rivers</p>
      <p class="contact__title">CEO</p>
      <p class="contact__row">
        <svg viewBox="0 0 10 10" aria-hidden="true"><path d="M2 1 L4 3 L3 4 Q4 6 6 7 L7 6 L9 8 L7.5 9.5 Q2 8 0.5 2.5 Z" fill="var(--text)"/></svg>
        888-555-0142
      </p>
      <p class="contact__row">
        <svg viewBox="0 0 10 10" aria-hidden="true"><rect x="0.5" y="2" width="9" height="6.5" fill="none" stroke="var(--text)"/><path d="M0.5 2 L5 5.5 L9.5 2" fill="none" stroke="var(--text)"/></svg>
        hello@veluxabone.com
      </p>
      <p class="contact__row">
        <svg viewBox="0 0 10 10" aria-hidden="true"><circle cx="5" cy="5" r="4.3" fill="none" stroke="var(--text)"/><ellipse cx="5" cy="5" rx="1.8" ry="4.3" fill="none" stroke="var(--text)"/><path d="M0.7 5 H9.3" stroke="var(--text)"/></svg>
        veluxabonemotion.com
      </p>
      <div class="office">
        <p>Hialeah, City in Florida</p>
        <p class="office__phone">P : +330 555-0110</p>
      </div>
      <div class="office">
        <p>Homestead, City in Florida</p>
        <p class="office__phone">P : +330 555-0120</p>
      </div>
      <div class="office">
        <p>Tallahassee, City in Florida</p>
        <p class="office__phone">P : +330 555-0130</p>
      </div>
    </div>
  </section>

  <section class="card card--brand">
    <p class="brand-name">Veluxa<br>Bone &amp; Motion</p>
  </section>
</main>
</body>
</html>
```